International business needs business cards

Our company, DRV Ventures Inc. is in the business of supplying a range construction products with particular emphasis on CEMENT. We have developed our own brand - TORVAN SUPPLIES - with which to infiltrate the market. We are launching our brand of cement (TORVAN Type IS Cement) into the Caribbean which is unlike anything this market has ever seen. A monopoly has existed here for the past 60-odd years and the market has now opened to allow the importation of other brands and consumers are anxious and ready for change/improvement. We are very excited to be launching and want to make a great first impression. We will be conducting workshops and seminars (from government level to the hardware store owners) and we want our business card to give us the strong, confident introduction that we need.

Target Market(s)

construction; builders; engineers; home owners

Industry/Entity Type

Construction

Contact Information for Business Card

Marisol Depree
CEO
cell # 1 555 4180736
Ground floor,Lindell Plaza Suite 2734
George Town,Grand Cayman
Cayman Islands,KY1-4823
EMAIL: m.depree@drvventuresinc.example
web site drvventuresinc.example

COMPANY: skype info drv.ventures.example

second card
Yvette Brannock-Depree
CFO
CELL# 1 555 607 3941
George Town,Grand Cayman
Cayman Islands,KY1-4823
EMAIL: y.brannockdepree@drvventuresinc.example
website drvventuresinc.example

Requirements
Must have
• Business cards must display BOTH logos - DRV is the company and TORVAN is the brand.

```html
<!DOCTYPE html>
<html lang="en">
<head>
<meta charset="utf-8">
<title>DRV Ventures Inc. — Business Card</title>
<link rel="stylesheet" href="https://fonts.googleapis.com/css2?family=Source+Sans+3:wght@400;600;700&display=swap">
<style>
  :root {
    --stage: #8f8f8f;
    --paper: #f1f1f1;
    --maroon: #6b1216;
    --ink: #1a1a1a;
    --muted: #555555;
    --white: #ffffff;
  }
  * { box-sizing: border-box; margin: 0; padding: 0; }
  html, body {
    width: 1105px;
    height: 1200px;
    overflow: hidden;
  }
  body {
    background: var(--stage);
    font-family: "Source Sans 3", "Myriad Pro", Arial, sans-serif;
    position: relative;
  }
  .card {
    position: absolute;
    left: 180px;
    width: 746px;
    height: 427px;
  }
  .card--front { top: 119px; background: var(--paper); color: var(--muted); }
  .card--back { top: 637px; background: var(--maroon); color: var(--white); }

  .brand {
    position: absolute;
    top: 30px;
    right: 30px;
    display: flex;
    align-items: center;
    gap: 14px;
  }
  .brand__square {
    width: 62px;
    height: 62px;
    background: var(--maroon);
  }
  .brand__name {
    font-size: 34px;
    font-weight: 700;
    color: var(--ink);
    line-height: 1;
  }

  .accent-bar {
    position: absolute;
    left: 0;
    top: 228px;
    width: 11px;
    height: 61px;
    background: var(--maroon);
  }
  .person {
    position: absolute;
    left: 29px;
    top: 228px;
  }
  .person__name {
    font-size: 28px;
    font-weight: 600;
    color: var(--maroon);
    line-height: 1.1;
  }
  .person__title {
    font-size: 20px;
    color: var(--ink);
    line-height: 1.3;
  }

  .address, .contact {
    position: absolute;
    font-size: 19.5px;
    line-height: 27px;
    font-style: normal;
  }
  .address { left: 29px; top: 297px; }
  .contact { left: 334px; top: 324px; }
  .contact__label { color: var(--maroon); font-weight: 700; }

  .brand-mark {
    position: absolute;
    left: 50%;
    top: 180px;
    transform: translateX(-50%);
    font-size: 52px;
    font-weight: 700;
    letter-spacing: 4px;
    color: var(--white);
  }
  .back-url {
    position: absolute;
    left: 0;
    right: 0;
    top: 378px;
    text-align: center;
    font-size: 19px;
  }
</style>
</head>
<body>
  <section class="card card--front" aria-label="Business card front">
    <div class="brand">
      <span class="brand__square" aria-hidden="true"></span>
      <span class="brand__name">DRV Ventures Inc.</span>
    </div>

    <span class="accent-bar" aria-hidden="true"></span>
    <div class="person">
      <p class="person__name">Marisol Depree</p>
      <p class="person__title">CEO</p>
    </div>

    <address class="address">
      Ground floor<br>
      Lindell Plaza Suite 2734<br>
      George Town,Grand Cayman<br>
      Cayman Islands,KY1-4823
    </address>

    <div class="contact">
      <p><span class="contact__label">Mobile:</span>1 555 4180736</p>
      <p>m.depree@drvventuresinc.example</p>
      <p>www.drvventuresinc.example</p>
    </div>
  </section>

  <section class="card card--back" aria-label="Business card back">
    <p class="brand-mark">TORVAN</p>
    <p class="back-url">www.drvventuresinc.example</p>
  </section>
</body>
</html>
```